Visualisation Software brochure

i need a sales brochure for a new visualisation software company called Lumora Studio Max.
The software has been specifically designed for manufacturers, distributers and retailers in the design / décor / furnishing / building industries. It allows customers can then import unlimited numbers of digital photos of rooms from their own home or take advantage of a library of pre-made photos, and then render different products from your catalogue into that photo to see what the finished look will be.
i have attached:
1) a mock up of the home page of the website
2) example of brochure wording that i have put together (although i am a little unsure about what other words i can add - so any suggestions here would be good)
3) i have attached some examples of other brochures that i like and would like similar designs
I am after a classy brochure used by a large corporate technology company that is given to executives and gives an impression of quality, trustworthiness and innovation.
• the colour blue as per the colours on my website mock up provided in the design brief
• I like simple, smart, clean and uncluttered design
• I like simple, clean and uncluttered design
• I like pictures that fit in with my technology (whether that be home and interior design, mixing virtual world and real world, visualising an idea) rather than basic stock of corporate people
Updates
Target Market(s)
marketing professionals
Industry/Entity Type
Software
Font styles to use
Look and feel
Each slider illustrates characteristics of the customer's brand and the style your logo design should communicate.

```html
<!DOCTYPE html>
<html lang="en">
<head>
<meta charset="utf-8">
<title>Lumora Studio Max – Brochure</title>
<link rel="stylesheet" href="https://fonts.googleapis.com/css2?family=Titillium+Web:wght@200;300;400;600&display=swap">
<style>
  :root {
    --page-bg: #f4f4f4;
    --brand-blue: #2d93f5;
    --accent-blue: #4aa3f7;
    --white: #ffffff;
    --ink: #111111;
    --navy: #1b2a4e;
    --photo-light: #e4e4e4;
    --photo-mid: #a9a9a9;
    --photo-dark: #5b5b5b;
  }
  * { margin: 0; padding: 0; box-sizing: border-box; }
  html, body { width: 1200px; height: 838px; overflow: hidden; }
  body {
    background: var(--page-bg);
    font-family: "Titillium Web", sans-serif;
    position: relative;
  }
  .panel {
    position: absolute;
    top: 38px;
    width: 537px;
    height: 759px;
    box-shadow: 0 4px 18px rgba(0,0,0,0.12);
  }
  .panel--back { left: 59px; background: var(--brand-blue); color: var(--white); }
  .panel--front { left: 604px; background: var(--white); }

  .brand-mark {
    position: absolute;
    display: flex; align-items: center; justify-content: center;
    border-radius: 50%;
    background: var(--white);
    color: var(--brand-blue);
    font-weight: 600;
  }
  .panel--back .brand-mark { left: 92px; top: 62px; width: 100px; height: 100px; font-size: 34px; }
  .panel--front .brand-mark {
    left: 445px; top: 667px; width: 66px; height: 66px; font-size: 22px;
    background: var(--brand-blue); color: var(--white);
  }

  .bracket { position: absolute; left: 185px; top: 164px; }

  .about { position: absolute; left: 218px; top: 266px; width: 274px; }
  .about__title { font-size: 23px; font-weight: 300; margin-bottom: 12px; }
  .about__text {
    font-size: 14px; font-weight: 200; line-height: 21px;
    text-align: justify; hyphens: auto; margin-bottom: 21px;
  }

  .contact { position: absolute; left: 218px; top: 637px; color: var(--navy); }
  .contact__title { font-size: 16px; font-weight: 400; margin-bottom: 6px; }
  .contact__line { font-size: 13px; font-weight: 300; line-height: 20px; }
  .contact__label { display: inline-block; width: 22px; }

  .hero-photo {
    position: absolute; left: 0; top: 0; width: 537px; height: 320px;
    background: linear-gradient(100deg, var(--photo-light) 0%, var(--photo-mid) 45%, var(--photo-dark) 75%, var(--photo-light) 100%);
  }
  .tagline-box {
    position: absolute; left: 218px; top: 341px; width: 294px; height: 143px;
    background: var(--brand-blue); color: var(--white);
    padding: 26px 10px 0 10px;
    font-size: 25px; font-weight: 300; line-height: 29px;
  }
  .tagline-box strong { font-weight: 600; }
  .headline {
    position: absolute; left: 28px; top: 518px;
    font-size: 39px; font-weight: 400; letter-spacing: 0.5px; color: var(--ink);
  }
  .subline {
    position: absolute; left: 28px; top: 574px;
    font-size: 30px; font-weight: 200; line-height: 34px; color: var(--accent-blue);
    letter-spacing: 0.3px;
  }
</style>
</head>
<body>
  <section class="panel panel--back">
    <div class="brand-mark">LSM</div>
    <svg class="bracket" width="20" height="430" viewBox="0 0 20 430" aria-hidden="true">
      <path d="M0 1 H17 V428 H24" fill="none" stroke="#ffffff" stroke-width="1.5"/>
    </svg>
    <div class="about">
      <h2 class="about__title">About Lumora Studio Max</h2>
      <p class="about__text">Formed in 2013 based on a growing need in the market for a fully functional tool</p>
      <p class="about__text">Many other products offer big promises but their short comings impede the success of the retailers. Our goal is to ensure a premium experience for customers and retailers.</p>
      <p class="about__text">We are very focused to be the obvious leader in this space.</p>
      <p class="about__text">This is based upon our 12 point methodology to maximise customer satisfaction to 95% percentile and beyond.</p>
    </div>
    <div class="contact">
      <h3 class="contact__title">CONTACT</h3>
      <p class="contact__line"><span class="contact__label">M:</span>xxx xxx xxx</p>
      <p class="contact__line"><span class="contact__label">E:</span>info@lumorastudiomax.com</p>
      <p class="contact__line"><span class="contact__label">W:</span>www.lumorastudiomax.com</p>
    </div>
  </section>

  <section class="panel panel--front">
    <div class="hero-photo" role="img" aria-label="Photo of a grey modern living room with shelving and sofa, a hand holding a smartphone that shows the room"></div>
    <div class="tagline-box">Let <strong>your clients</strong><br>visualise <strong>your products</strong><br>(literally)</div>
    <h1 class="headline">LUMORA STUDIO MAX</h1>
    <p class="subline">LEADING THE WAY<br>IN VISUALISATION SOFTWARE</p>
    <div class="brand-mark">LSM</div>
  </section>
</body>
</html>
```